Brochure 2 fold and Trifold

We need 2 types of brochure (2 fold and Trifold) design for our Brand "VELVET DAWN" Logo (La douceur de Mirelle) is in rose gold color
Target Market(s)
Women ages 17 and up
Industry/Entity Type
Supplement
Font styles to use
Serif
Script
Requirements
Must have
- Rose gold color tone make it look premium, minimalist look

```html
<!DOCTYPE html>
<html lang="en">
<head>
<meta charset="utf-8">
<title>VELVET DAWN – Skin Whitening & Sun Protection Brochure</title>
<link href="https://fonts.googleapis.com/css2?family=Sacramento&family=Montserrat:wght@600;700;800&family=Didact+Gothic&display=swap" rel="stylesheet">
<style>
  :root {
    --rose: #f1c6b4;
    --rose-deep: #ecb8a3;
    --rose-text: #e8a98f;
    --white: #ffffff;
    --ink: #555555;
    --ink-soft: #777777;
    --bar-blue: #5b8fd6;
    --bar-red: #c9504b;
    --bar-orange: #ee7b30;
    --photo-light: #f4f4f4;
    --photo-mid: #cfcfcf;
  }
  * { margin: 0; padding: 0; box-sizing: border-box; }
  html, body { width: 1200px; height: 840px; overflow: hidden; background: var(--white); }
  .brochure { position: relative; width: 1200px; height: 840px; overflow: hidden; background: var(--white); font-family: "Didact Gothic", sans-serif; }

  /* Left panel */
  .panel-ingredients { position: absolute; left: 0; top: 0; width: 410px; height: 840px; background: var(--rose); color: var(--white); }
  .title-script { position: absolute; left: 10px; top: 22px; font-family: "Sacramento", cursive; font-size: 104px; line-height: 1; color: var(--white); white-space: nowrap; transform: scale(0.76, 1.12); transform-origin: left top; }
  .title-bold { position: absolute; left: 22px; top: 126px; font-family: "Montserrat", sans-serif; font-weight: 800; font-size: 33px; letter-spacing: 0.5px; color: var(--white); white-space: nowrap; }
  .ingredient { position: absolute; left: 22px; width: 372px; }
  .ingredient h2 { display: inline-block; background: var(--white); color: var(--rose-text); font-family: "Montserrat", sans-serif; font-weight: 700; font-size: 16px; padding: 2px 10px 2px 4px; margin-bottom: 6px; }
  .ingredient p { font-size: 17.5px; line-height: 23px; text-align: justify; }
  .ingredient--phyto { top: 228px; }
  .ingredient--fern { top: 437px; }
  .ingredient--cysteine { top: 646px; }

  /* Middle panel */
  .panel-benefits { position: absolute; left: 410px; top: 0; width: 395px; height: 840px; }
  .portrait { position: absolute; inset: 0; background: linear-gradient(160deg, var(--photo-mid) 0%, var(--photo-light) 45%, #e6e6e6 70%, var(--photo-light) 100%); }
  .frame { position: absolute; left: 18px; top: 24px; width: 362px; height: 806px; border: 2px solid var(--rose); }
  .benefits-script { position: absolute; left: 48px; top: 462px; font-family: "Sacramento", cursive; font-size: 92px; line-height: 1; color: var(--rose); white-space: nowrap; transform: scaleX(0.68); transform-origin: left top; }
  .benefits-brand { position: absolute; left: 50px; top: 538px; color: var(--rose); white-space: nowrap; }
  .benefits-brand .of { font-family: "Sacramento", cursive; font-size: 40px; }
  .benefits-brand .name { font-family: "Montserrat", sans-serif; font-weight: 800; font-size: 27px; }
  .benefit-list { position: absolute; left: 56px; top: 590px; width: 280px; height: 230px; background: var(--rose); list-style: none; padding: 8px 10px 0 12px; }
  .benefit-list li { position: relative; padding-left: 20px; color: var(--white); font-size: 17px; line-height: 19px; margin-bottom: 12px; }
  .benefit-list li::before { content: ""; position: absolute; left: 0; top: 4px; width: 11px; height: 11px; border-radius: 50%; background: var(--white); }

  /* Right panel */
  .panel-studies { position: absolute; left: 805px; top: 0; width: 395px; height: 840px; background: linear-gradient(90deg, #f7e6df 0%, var(--white) 6%); }
  .studies-title { position: absolute; left: 73px; top: 10px; width: 245px; height: 46px; background: var(--rose); color: var(--white); font-family: "Montserrat", sans-serif; font-weight: 700; font-size: 23px; text-align: center; line-height: 46px; white-space: nowrap; }
  .chart-skin { position: absolute; left: 28px; top: 118px; }
  .chart-melasma { position: absolute; left: 72px; top: 500px; }
  .study-text { position: absolute; left: 32px; width: 332px; font-size: 17px; line-height: 20px; color: var(--ink); text-align: justify; }
  .study-text--skin { top: 360px; text-align: left; }
  .study-text--melasma { top: 683px; }
  .citation { position: absolute; left: 32px; width: 332px; font-size: 15.5px; line-height: 19px; font-style: italic; color: var(--ink-soft); }
  .citation--skin { top: 446px; }
  .citation--melasma { top: 768px; }
</style>
</head>
<body>
<div class="brochure">

  <section class="panel-ingredients">
    <div class="title-script">skin whitening</div>
    <div class="title-bold">&amp;SUN PROTECTION</div>

    <article class="ingredient ingredient--phyto">
      <h2>1.PhytoBLOOM</h2>
      <p>An award winning natural supplement using non-GMO tomato species rich in colourless carotenoids, phytoene and phytofluene. This patented combination provides superior whitening, UVA and UVB protection, anti-inflammatory and antioxidant properties.</p>
    </article>

    <article class="ingredient ingredient--fern">
      <h2>2.Polypodium leucotomos</h2>
      <p>Naturally extracted from a tropical natural fern found in the Americas, it has been used for centuries by the natives for its superior benefits. Now clinically proven to protect against UV radiation due to its antioxidant, anti-inflammatory and DNA repair abilities.</p>
    </article>

    <article class="ingredient ingredient--cysteine">
      <h2>3.L-Cysteine</h2>
      <p>A potent amino acid that has very high skin-whitening abilities. It prevents the production of pigment cells when the skin is exposed to UV rays and stimulates the production of Glutathione, another strong skin-whitening antioxidant.</p>
    </article>
  </section>

  <section class="panel-benefits">
    <div class="portrait" role="img" aria-label="Soft black and white close-up portrait photograph of a woman's face"></div>
    <div class="frame"></div>
    <div class="benefits-script">Benefits</div>
    <div class="benefits-brand"><span class="of">of </span><span class="name">VELVET DAWN</span></div>
    <ul class="benefit-list">
      <li>Skin Whitening</li>
      <li>Collagen Protection</li>
      <li>DNA Repair</li>
      <li>Prevents Against<br>Premature Skin Aging</li>
      <li>Enhanced Antioxidant<br>&amp; Anti-inflammatory effects</li>
      <li>Natural UV Protection effects</li>
    </ul>
  </section>

  <section class="panel-studies">
    <div class="studies-title">CLINICAL STUDIES</div>

    <svg class="chart-skin" width="340" height="180" viewBox="0 0 340 180" font-family="Didact Gothic, sans-serif">
      <text x="170" y="10" font-size="8" text-anchor="middle" fill="#444">Average clinical improvement of skin parameters</text>
      <g stroke="#e2e2e2" stroke-width="0.7">
        <line x1="20" y1="20" x2="335" y2="20"/><line x1="20" y1="33" x2="335" y2="33"/>
        <line x1="20" y1="46" x2="335" y2="46"/><line x1="20" y1="59" x2="335" y2="59"/>
        <line x1="20" y1="72" x2="335" y2="72"/><line x1="20" y1="85" x2="335" y2="85"/>
        <line x1="20" y1="98" x2="335" y2="98"/><line x1="20" y1="111" x2="335" y2="111"/>
        <line x1="20" y1="124" x2="335" y2="124"/><line x1="20" y1="137" x2="335" y2="137"/>
        <line x1="20" y1="150" x2="335" y2="150"/>
      </g>
      <g font-size="5" fill="#666" text-anchor="end">
        <text x="16" y="22">100</text><text x="16" y="48">80</text><text x="16" y="74">60</text>
        <text x="16" y="100">40</text><text x="16" y="126">20</text><text x="16" y="152">0</text>
      </g>
      <g fill="var(--bar-blue)">
        <rect x="38" y="91.5" width="15" height="58.5"/>
        <rect x="101" y="66.8" width="15" height="83.2"/>
        <rect x="164" y="72" width="15" height="78"/>
        <rect x="227" y="116.2" width="15" height="33.8"/>
        <rect x="290" y="112.3" width="15" height="37.7"/>
      </g>
      <g fill="var(--bar-red)">
        <rect x="55" y="59" width="15" height="91"/>
        <rect x="118" y="51.2" width="15" height="98.8"/>
        <rect x="181" y="33" width="15" height="117"/>
        <rect x="244" y="85" width="15" height="65"/>
        <rect x="307" y="70.7" width="15" height="79.3"/>
      </g>
      <g font-size="5" fill="#555" text-anchor="middle">
        <text x="54" y="158">Dryness</text><text x="117" y="158">Roughness</text>
        <text x="180" y="158">Suppleness</text><text x="243" y="158">Complexion evenness</text>
        <text x="306" y="158">Texture</text>
      </g>
      <rect x="140" y="164" width="4" height="4" fill="var(--bar-blue)"/>
      <text x="146" y="168" font-size="4.5" fill="#555">Day 42</text>
      <rect x="168" y="164" width="4" height="4" fill="var(--bar-red)"/>
      <text x="174" y="168" font-size="4.5" fill="#555">Day 84</text>
      <text x="170" y="178" font-size="4.5" fill="#555" text-anchor="middle">Figure 3. Graphic summary of the average changes in clinical scores</text>
    </svg>

    <p class="study-text study-text--skin">Skin improvement results of a clinical study conducted by dermatologists measuring skin quality after 12 weeks use of colourless carotenoids.</p>
    <p class="citation citation--skin">(Global Dermatology 2015: 2(4) Page178-182)</p>

    <svg class="chart-melasma" width="220" height="160" viewBox="0 0 220 160" font-family="Didact Gothic, sans-serif">
      <g stroke="#d9d9d9" stroke-width="1">
        <line x1="24" y1="33" x2="200" y2="33"/><line x1="24" y1="68" x2="200" y2="68"/>
        <line x1="24" y1="103" x2="200" y2="103"/>
      </g>
      <line x1="24" y1="138" x2="200" y2="138" stroke="#999" stroke-width="1"/>
      <g font-size="14" fill="#333" text-anchor="end">
        <text x="14" y="38">6</text><text x="14" y="73">4</text>
        <text x="14" y="108">2</text><text x="14" y="143">0</text>
      </g>
      <rect x="56" y="40" width="32" height="98" fill="var(--bar-blue)"/>
      <rect x="92" y="80" width="32" height="58" fill="var(--bar-orange)"/>
      <path d="M66 32 Q96 2 126 22" fill="none" stroke="var(--bar-orange)" stroke-width="6"/>
      <polygon points="119,14 135,28 118,33" fill="var(--bar-orange)"/>
      <text x="140" y="14" font-size="15" font-weight="700" fill="#222">- 42,1%</text>
      <text x="146" y="27" font-size="9" fill="#444">p &lt; 0,05</text>
    </svg>

    <p class="study-text study-text--melasma">Reduction in intensity of melasma with usage of daily oral Polypodium Leucotomos for 12 weeks with sunscreen SPF 45.</p>
    <p class="citation citation--melasma">(American Journal of Dermatology 2012: 66(4) Page AB21).</p>
  </section>

</div>
</body>
</html>
```